Request for Business Card Design

Hi. My name is Marlene, I am looking for a new business card design for my company, Quarrow Signal Instruments, LLC. I really like the design you did for Tarsel Venture and was hoping you could do something similar using our full logo and our mark. I am also open to any raised texture design using our mark. I have attached our full logo, which would need to be somewhere on the card, as well as the mark in both outline and full form, as well as our brand colors / guide. The card does not have to be white, as long as our logo and mark appear. I actually like darker colored business cards more, but am open to all options. If you are interested in working with me, please let me know. We would also take the business card design into letterhead design if you can do that.

```html
<!DOCTYPE html>
<html lang="en">
<head>
<meta charset="utf-8">
<title>Quarrow Signal Instruments – Business Card</title>
<link href="https://fonts.googleapis.com/css2?family=Barlow:wght@600&family=Open+Sans:ital,wght@0,400;0,600;1,600&display=swap" rel="stylesheet">
<style>
  :root {
    --backdrop: #2f2a27;
    --card: #161616;
    --accent: #0e9bc3;
    --ink: #ffffff;
    --ink-soft: #d9d9d9;
  }
  * { box-sizing: border-box; margin: 0; padding: 0; }
  html, body {
    width: 1200px; height: 716px; overflow: hidden;
    background: var(--backdrop);
  }
  .stage { position: relative; width: 1200px; height: 716px; }
  .card {
    position: absolute; top: 203px;
    width: 540px; height: 309px;
    background: var(--card);
    overflow: hidden;
    box-shadow: 0 12px 30px rgba(0,0,0,.45);
  }
  .card--front { left: 40px; }
  .card--back { left: 620px; }
  .accent-disc {
    position: absolute; width: 320px; height: 320px;
    border-radius: 50%; background: var(--accent); top: -3px;
  }
  .card--front .accent-disc { left: 400px; }
  .card--back .accent-disc { left: -180px; }

  .wordmark { position: absolute; display: flex; align-items: center; gap: 10px; color: var(--ink); font-family: "Barlow", sans-serif; font-weight: 600; }
  .wordmark__dot { border-radius: 50%; background: var(--accent); flex: none; }
  .wordmark__name { display: block; letter-spacing: .12em; line-height: 1; }
  .wordmark__tag { display: block; letter-spacing: .06em; line-height: 1.3; }

  .card--front .wordmark { left: 30px; top: 28px; }
  .card--front .wordmark__dot { width: 34px; height: 34px; }
  .card--front .wordmark__name { font-size: 26px; }
  .card--front .wordmark__tag { font-size: 8.5px; }

  .card--back .wordmark { right: 40px; top: 150px; }
  .card--back .wordmark__dot { width: 46px; height: 46px; }
  .card--back .wordmark__name { font-size: 36px; }
  .card--back .wordmark__tag { font-size: 11px; }

  .person { position: absolute; left: 30px; top: 96px; padding-left: 14px; border-left: 7px solid var(--accent); font-family: "Open Sans", sans-serif; }
  .person__name { color: var(--accent); font-style: italic; font-weight: 600; font-size: 17px; letter-spacing: .02em; line-height: 1.1; }
  .person__role { color: var(--ink-soft); font-size: 11px; }

  .contact { position: absolute; left: 51px; top: 150px; font-family: "Open Sans", sans-serif; color: var(--ink-soft); font-size: 11px; line-height: 1.55; list-style: none; }
  .contact__address { margin-bottom: 8px; }
  .contact__line { display: flex; align-items: center; gap: 6px; }
  .contact__icon { width: 10px; height: 10px; fill: var(--accent); flex: none; }
</style>
</head>
<body>
<main class="stage">
  <section class="card card--front" aria-label="Card front">
    <div class="accent-disc"></div>
    <div class="wordmark">
      <span class="wordmark__dot"></span>
      <span><span class="wordmark__name">QUARROW</span><span class="wordmark__tag">SIGNAL INSTRUMENTS</span></span>
    </div>
    <div class="person">
      <p class="person__name">DANA WHITLOW</p>
      <p class="person__role">Managing Director</p>
    </div>
    <ul class="contact">
      <li class="contact__address">Your address, City<br>State, Zip 1234</li>
      <li class="contact__line">
        <svg class="contact__icon" viewBox="0 0 10 10"><path d="M2 0.5l2 2-1 1.2a6 6 0 0 0 3.3 3.3l1.2-1 2 2-1.3 1.5C4 9.5 0.5 6 0.5 1.8z"/></svg>123 456 789</li>
      <li class="contact__line">
        <svg class="contact__icon" viewBox="0 0 10 10"><path d="M0.5 2h9v6h-9z M0.5 2l4.5 3.5L9.5 2" fill="none" stroke="#0e9bc3" stroke-width="1.2"/></svg>info@yourgmail.com</li>
      <li class="contact__line">
        <svg class="contact__icon" viewBox="0 0 10 10"><circle cx="5" cy="5" r="4.5"/><path d="M0.5 5h9M5 0.5c-2 2.5-2 6.5 0 9M5 0.5c2 2.5 2 6.5 0 9" fill="none" stroke="#161616" stroke-width=".8"/></svg>www.yourwebsite.com</li>
    </ul>
  </section>

  <section class="card card--back" aria-label="Card back">
    <div class="accent-disc"></div>
    <div class="wordmark">
      <span class="wordmark__dot"></span>
      <span><span class="wordmark__name">QUARROW</span><span class="wordmark__tag">SIGNAL INSTRUMENTS</span></span>
    </div>
  </section>
</main>
</body>
</html>
```